Custom Cabinet Shop Needs a website design

Hi,
We need a website for a Custom Cabinet Shop and Cabinet parts manufacturing business.
The business has two sides to it. One side provides custom Kitchens, vanities, entertainment units, offices and what not to homeowners and contractors.
The 2nd side of the business provides built to order cabinet boxes and other parts required to put together a project to other cabinet shops, small contractors looking to install there own cabinets.
Website will need a Gallery to display work.
Color scheme to go well with logo.
current website is www.brambleoakcustomcabinets.com
being changed to www.brambleoak.ca
Logo Included in attached files.
Tagline "Joinery with Spirit"
Mission Statement "Our passion is to deliver inspired cabinetry solutions to suit all your needs, supported by our phenomenal star class customer service"
The website should convey quality and professionalism.
Thank you.
Homeowners/ Contractors
Entertainment

```html
<!DOCTYPE html>
<html lang="en">
<head>
<meta charset="utf-8">
<title>Brambleoak Custom Cabinets</title>
<link rel="stylesheet" href="https://fonts.googleapis.com/css2?family=Fira+Sans+Condensed:wght@400;500&family=Open+Sans:wght@300;400;700&display=swap">
<style>
:root{
  --orange:#ef5a24;
  --dark:#1c1a19;
  --band:rgba(22,20,19,.92);
  --ink:#2a2a2a;
  --muted:#6b6b6b;
  --light:#f4f2ef;
  --white:#fff;
}
*{margin:0;padding:0;box-sizing:border-box}
html,body{width:863px;height:1200px;overflow:hidden;background:var(--white)}
body{position:relative;font-family:"Open Sans",sans-serif;color:var(--ink)}
.hero{position:absolute;left:0;top:0;width:863px;height:575px;
  background:linear-gradient(180deg,#9c8a78 0%,#5b3a2e 25%,#3c2420 55%,#6e5a4a 80%,#c9b8a4 100%)}
.brand{position:absolute;left:65px;top:25px;width:207px;height:68px;background:var(--white);
  clip-path:polygon(0 0,100% 0,96% 100%,0 100%);display:flex;align-items:center;padding-left:18px;gap:8px}
.brand-mark{width:22px;height:22px;background:var(--orange)}
.brand-name{font-family:"Fira Sans Condensed",sans-serif;font-weight:500;font-size:19px;color:var(--dark);letter-spacing:.5px}
.topnav{position:absolute;left:268px;top:30px;width:530px;height:57px;background:rgba(30,27,25,.9);
  display:flex;align-items:center;padding-left:34px}
.topnav a{font-family:"Fira Sans Condensed",sans-serif;color:var(--white);font-size:12.5px;text-decoration:none;margin-right:33px}
.social-sq{position:absolute;right:14px;top:20px;display:flex;gap:4px}
.social-sq span{width:18px;height:18px;background:var(--white)}
.caption{position:absolute;left:65px;top:477px;width:733px;height:98px;background:var(--band);padding:16px 15px}
.caption h1{font-weight:300;font-size:30px;color:var(--white);letter-spacing:-.5px;line-height:1}
.caption h1 b{font-weight:700}
.caption p{font-size:8.6px;color:#e6e6e6;line-height:14px;margin-top:8px;width:520px}
.btn-hero{position:absolute;left:584px;top:32px;width:134px;height:36px;background:var(--orange);color:var(--white);
  font-family:"Fira Sans Condensed",sans-serif;font-weight:500;font-size:12px;display:flex;align-items:center;justify-content:center;box-shadow:0 3px 0 #b8421a}
.features{position:absolute;left:65px;top:575px;width:733px;height:185px;background:var(--white);
  box-shadow:0 8px 14px -6px rgba(0,0,0,.25);display:flex;padding:38px 14px 0}
.feature{width:242px;position:relative}
.feature h2{font-family:"Fira Sans Condensed",sans-serif;font-weight:500;font-size:13.5px;color:var(--dark);padding-left:21px;position:relative}
.feature h2::before{content:"";position:absolute;left:0;top:2px;width:5px;height:13px;background:var(--orange)}
.feature .body{margin-top:26px;border-left:4px dotted #e2e2e2;padding-left:17px;height:113px}
.feature p{font-size:8.6px;color:var(--muted);line-height:15.8px;width:205px}
.btn-small{position:absolute;right:12px;bottom:0;background:var(--dark);color:var(--white);font-family:"Fira Sans Condensed",sans-serif;font-size:9.5px;padding:6px 9px}
.gallery{position:absolute;left:0;top:790px;width:863px;height:262px;background:var(--light)}
.gallery h3{position:absolute;left:79px;top:28px;font-family:"Fira Sans Condensed",sans-serif;font-weight:500;font-size:13.5px;color:var(--dark)}
.gallery .rule{position:absolute;left:165px;top:38px;width:590px;border-top:3px dotted #ddd}
.arrows{position:absolute;left:758px;top:32px;display:flex;gap:2px}
.arrows span{width:12px;height:12px;background:#555;display:flex;align-items:center;justify-content:center}
.arrows span:last-child{background:var(--dark)}
.thumbs{position:absolute;left:80px;top:66px;display:flex;gap:14px}
.thumb{width:165px;text-align:center}
.thumb .ph{height:122px}
.thumb h4{font-family:"Fira Sans Condensed",sans-serif;font-weight:400;font-size:11.5px;color:#333;margin-top:6px}
.thumb small{display:block;font-size:7px;color:#999;margin-top:2px}
.thumb .line{height:2px;background:#cfcfcf;margin-top:6px}
.thumb.active h4{color:var(--orange)}
.thumb.active .line{background:var(--orange)}
.footer{position:absolute;left:0;top:1055px;width:863px;height:145px;background:var(--dark);text-align:center}
.footnav{margin-top:29px;display:flex;justify-content:center;gap:29px}
.footnav a{font-family:"Open Sans",sans-serif;font-size:10px;color:var(--white);text-decoration:none}
.footnav a.current{font-weight:700}
.social-circ{display:flex;justify-content:center;gap:6px;margin-top:19px}
.social-circ span{width:20px;height:20px;border-radius:50%;background:var(--white)}
.copy{font-size:8px;color:var(--white);margin-top:15px}
</style>
</head>
<body>
<div class="hero" role="img" aria-label="Photo of a luxury kitchen with dark wood cabinets, granite island and arched window"></div>
<header>
  <div class="brand"><span class="brand-mark"></span><span class="brand-name">BRAMBLEOAK</span></div>
  <nav class="topnav">
    <a href="#">Home</a><a href="#">Our Gallery</a><a href="#">Our Services</a><a href="#">Warranty</a><a href="#">Contact Us</a>
    <div class="social-sq"><span></span><span></span><span></span><span></span></div>
  </nav>
</header>
<section class="caption">
  <h1>JOINERY WITH <b>SPIRIT</b></h1>
  <p>Lorem ipsum dolor sit amet, consectetur adipiscing elit sed do eiusmod tempor incididunt ut labore et dolore enim minim veniam, quis nostrud exercitation ullamco laboris nisi ut aliquip ex ea commodo consequat dolor in reprehenderit .</p>
  <div class="btn-hero">READ MORE</div>
</section>
<section class="features">
  <div class="feature"><h2>ABOUT US</h2><div class="body"><p>Lorem ipsum dolor sit amet, consectetur adipiscing elit, sed do eiusmod tempor incididunt ut labore et dolore magna aliqua. Ut enim ad minim veniam, quis nostrud exercitation ullamco laboris nisi ut aliquip ex ea commodo consequat. Duis aute irure dolor in reprehenderit in voluptate velit esse</p></div></div>
  <div class="feature"><h2>FINEST QUALITY MATERIALS</h2><div class="body"><p>Lorem ipsum dolor sit amet, consectetur adipiscing elit, sed do eiusmod tempor incididunt ut labore et dolore magna aliqua enim ad minim veniam is quis exercitation ullamco.</p><span class="btn-small">Read More</span></div></div>
  <div class="feature"><h2>RESIDENTIAL</h2><div class="body"><p>Here at Brambleoak Custom Cabinets we are proud to be involved in the custom cabinet market. By employing and partnering up with local artisans we are able to deliver a product.</p><span class="btn-small">Read More</span></div></div>
</section>
<section class="gallery">
  <h3>OUR GALLERY</h3><div class="rule"></div>
  <div class="arrows"><span><svg width="6" height="8"><path d="M5 0L1 4l4 4" stroke="#fff" fill="none"/></svg></span><span><svg width="6" height="8"><path d="M1 0l4 4-4 4" stroke="#fff" fill="none"/></svg></span></div>
  <div class="thumbs">
    <div class="thumb"><div class="ph" role="img" aria-label="Kitchen with cherry cabinets and wood floor" style="background:linear-gradient(#c9b9a6,#6a2f22)"></div><h4>Lorem Ipsum Dolor</h4><small>Lorem ipsum</small><div class="line"></div></div>
    <div class="thumb active"><div class="ph" role="img" aria-label="Gallery image with zoom overlay" style="background:#141414;display:flex;align-items:center;justify-content:center"><svg width="30" height="30" viewBox="0 0 30 30"><circle cx="12" cy="12" r="9" stroke="#fff" stroke-width="3" fill="none"/><path d="M19 19l8 8M12 7v10M7 12h10" stroke="#fff" stroke-width="3"/></svg></div><h4>Sit Amet Consectetur</h4><small>Lorem ipsum</small><div class="line"></div></div>
    <div class="thumb"><div class="ph" role="img" aria-label="Kitchen with red wood cabinets and island" style="background:linear-gradient(#b96a4a,#7a2a1c)"></div><h4>Adipisicing Elit</h4><small>Lorem ipsum</small><div class="line"></div></div>
    <div class="thumb"><div class="ph" role="img" aria-label="Open kitchen with brown cabinets and island" style="background:linear-gradient(#d3cbc0,#6e4a38)"></div><h4>Labore Et Dolore</h4><small>Lorem ipsum</small><div class="line"></div></div>
  </div>
</section>
<footer class="footer">
  <nav class="footnav"><a class="current" href="#">Home</a><a href="#">Our Gallery</a><a href="#">Our Services</a><a href="#">Warranty</a><a href="#">Contact Us</a></nav>
  <div class="social-circ"><span></span><span></span><span></span><span></span><span></span><span></span></div>
  <p class="copy">Copyrights © 2015. Brambleoak Custom Cabinets . All Rights Reserved</p>
</footer>
</body>
</html>
```